Business card for denture clinic Veltrimora

We need a new business card with our new logo. We are a denture clinic in New Zealand with our target market being 45+ years old. We would need a space on the back to write our patients next appointment on. We would space for only one appointment rather than a list. We will attach a photo showing an example of this. But of course, we would like to see your twist on this. We want it to be bold and easy to read and a good mixture of professional but modern. We have attached our logo to be used on the card.

Target Market(s)

People aged 45+ needing dentures

Industry/Entity Type

Dental

Contact Information for Business Card

We want our logo on the front and the space to write an appointment on the back. I've attached an example our our old business card showing this. We need to have the technicians details on the front.

Font styles to use
Sans Serif

Colors
0255a3
919191
fbfbfb

Requirements
Must have
• The following details:
• Liam Dorsett BDT, PGDipCDentTech Calverin
• Dental Prosthetist
• Phone numbers: 0800 47 3125
• 09 572 1394
• Email: liam@veltrimora.co.nz
• www.veltrimora.co.nz
• Address: 14 Marlow Crest Road
• Halbrook West
• Auckland 0793
Nice to have
• We would like our business cards to have more than just two colours as we want them to be more vibrant. We have uploaded an example of a business card we liked that showed this.

```html
<!DOCTYPE html>
<html lang="en">
<head>
<meta charset="utf-8">
<title>Veltrimora Business Card</title>
<link href="https://fonts.googleapis.com/css2?family=Questrial&display=swap" rel="stylesheet">
<style>
  :root {
    --bg: #2a2f36;
    --card-white: #fbfbfb;
    --brand-blue: #0268b4;
    --accent-yellow: #fcf23f;
    --accent-orange: #fc6b47;
    --tag-grey: #6f6f6f;
    --field-grey: #ecebee;
    --text-white: #ffffff;
  }
  * { margin: 0; padding: 0; box-sizing: border-box; }
  html, body { width: 1200px; height: 938px; overflow: hidden; }
  body {
    background: var(--bg);
    font-family: "Questrial", sans-serif;
    position: relative;
  }
  .card {
    position: absolute;
    top: 159px;
    width: 360px;
    height: 620px;
    border-radius: 26px;
    overflow: hidden;
    background: var(--card-white);
    box-shadow: 0 14px 30px rgba(0,0,0,0.45);
  }
  .card--back { left: 170px; }
  .card--front { left: 670px; }
  .card__bg { position: absolute; inset: 0; }
  .card__trim {
    position: absolute;
    inset: 14px;
    border: 1px solid rgba(0,0,0,0.35);
    border-radius: 18px;
  }
  .brand {
    position: absolute;
    left: 0; right: 0;
    text-align: center;
  }
  .brand__row {
    display: inline-flex;
    align-items: center;
    gap: 10px;
  }
  .brand__square {
    width: 26px; height: 26px;
    background: var(--brand-blue);
  }
  .brand__name {
    color: var(--brand-blue);
    font-size: 32px;
    letter-spacing: 1px;
    text-transform: uppercase;
  }
  .brand__tagline {
    display: block;
    margin-top: 8px;
    color: var(--tag-grey);
    font-size: 13px;
    letter-spacing: 3px;
    text-transform: uppercase;
  }
  .card--back .brand { top: 120px; }
  .card--front .brand { top: 62px; }

  .appointment {
    position: absolute;
    top: 470px;
    left: 40px;
    right: 40px;
    display: flex;
    flex-direction: column;
    gap: 24px;
  }
  .appointment__field {
    height: 40px;
    border-radius: 20px;
    background: var(--field-grey);
    color: var(--brand-blue);
    font-size: 14px;
    padding: 6px 18px;
  }

  .technician {
    position: absolute;
    left: 34px;
    top: 200px;
    color: var(--text-white);
  }
  .technician__role { font-size: 14px; }
  .technician__name {
    color: var(--accent-yellow);
    font-size: 28px;
    font-weight: 400;
    letter-spacing: 1px;
    text-transform: uppercase;
    margin: 4px 0 6px;
  }
  .technician__quals { font-size: 13px; }

  .address {
    position: absolute;
    right: 34px;
    top: 382px;
    color: var(--text-white);
    font-size: 15px;
    font-style: normal;
    line-height: 1.35;
    text-align: right;
  }
  .contact {
    position: absolute;
    left: 34px;
    top: 466px;
  }
  .contact__phones {
    color: var(--accent-yellow);
    font-size: 21px;
    letter-spacing: 0.5px;
  }
  .contact__email,
  .contact__web {
    color: var(--text-white);
    font-size: 14px;
    margin-top: 8px;
  }
</style>
</head>
<body>

  <section class="card card--back" aria-label="Card back">
    <svg class="card__bg" viewBox="0 0 360 620" preserveAspectRatio="none" aria-hidden="true">
      <path d="M0 392 Q200 360 360 222 L360 620 L0 620 Z" fill="var(--accent-yellow)"/>
      <path d="M0 414 Q210 380 360 236 L360 620 L0 620 Z" fill="var(--accent-orange)"/>
    </svg>
    <div class="card__trim"></div>
    <div class="brand">
      <span class="brand__row"><span class="brand__square"></span><span class="brand__name">Veltrimora</span></span>
      <span class="brand__tagline">The Denture Experts</span>
    </div>
    <div class="appointment">
      <div class="appointment__field">Date</div>
      <div class="appointment__field">Time</div>
    </div>
  </section>

  <section class="card card--front" aria-label="Card front">
    <svg class="card__bg" viewBox="0 0 360 620" preserveAspectRatio="none" aria-hidden="true">
      <path d="M0 170 Q260 170 360 280 L360 620 L0 620 Z" fill="var(--brand-blue)"/>
      <path d="M0 378 Q200 338 360 240 L360 620 L0 620 Z" fill="var(--accent-yellow)"/>
      <path d="M0 400 Q215 358 360 252 L360 620 L0 620 Z" fill="var(--accent-orange)"/>
    </svg>
    <div class="card__trim"></div>
    <div class="brand">
      <span class="brand__row"><span class="brand__square"></span><span class="brand__name">Veltrimora</span></span>
      <span class="brand__tagline">The Denture Experts</span>
    </div>
    <div class="technician">
      <p class="technician__role">Dental Prosthetist</p>
      <h1 class="technician__name">Liam Dorsett</h1>
      <p class="technician__quals">BDT, PGDipCDentTech Calverin</p>
    </div>
    <address class="address">
      14 Marlow Crest Road<br>
      Halbrook West<br>
      Auckland 0793
    </address>
    <div class="contact">
      <p class="contact__phones">0800 47 3125 / 09 572 1394</p>
      <p class="contact__email">liam@veltrimora.co.nz</p>
      <p class="contact__web">www.veltrimora.co.nz</p>
    </div>
  </section>

</body>
</html>
```